Business card for Eyelash extension salon in Rosewind Hills,California USA

We need new business card for our salon in Rosewind Hills. The salon name is 'Lashvera' . We would like to have...Business name: Lashvera Name of person: will provide later Address 4720 N.Alder Crest Ave Rosewind Hills , CA 90210 Phone: will provide later (Text only) Web: www.lashverastudio.example Snapgrid icon, Circlebook icon follow us for seasonal campaign and news @lashverastudiolounge Design should look elegant, high-end, clean, simple, cohesive with my brand. Please refer my brand board. Business name color will be metallic bronzy color. Im thinking grey background or white background. Thanks

Target Market(s)

25-35. Gender neutral. People who are in Entertainment business industry.
This is High-end Eyelash extension salon in Rosewind Hills

Industry/Entity Type

Beauty Salon

Contact Information for Business Card

Business name: Lashvera
Name of person: will provide later
Address 4720 N.Alder Crest Ave Rosewind Hills , CA 90210
Phone: will provide later (Text only)
Web: www.lashverastudio.example
Snapgrid icon, Circlebook icon
follow us for seasonal campaign and news @lashverastudiolounge

Requirements
Must have
• Beautiful, elegant, clean and simple look but very attractive and modern
Should not have
• We don't like too clutter, too busy designs.

```html
<!DOCTYPE html>
<html lang="en">
<head>
<meta charset="utf-8">
<title>Lashvera Business Card</title>
<link rel="stylesheet" href="https://fonts.googleapis.com/css2?family=Cormorant+Garamond:wght@400;500;600&family=Playfair+Display:wght@600&family=Montserrat:wght@500&display=swap">
<style>
  :root {
    --canvas: #e9e9e7;
    --bronze: #8b6a50;
    --ink: #3c3c3c;
    --muted: #a7a7a7;
    --card-white: #f4f4f2;
    --marble-a: #fbfbfa;
    --marble-b: #dcdcdc;
  }
  * { margin: 0; padding: 0; box-sizing: border-box; }
  html, body { width: 1200px; height: 960px; overflow: hidden; }
  body { background: var(--canvas); position: relative; font-family: "Cormorant Garamond", Georgia, serif; color: var(--ink); font-variant-numeric: lining-nums; }

  .card { position: absolute; width: 601px; height: 343px; }

  /* Front */
  .card-front { left: 302px; top: 122px; background: var(--bronze); }
  .marble-field {
    position: absolute; inset: 14px 15px 16px 14px;
    background: radial-gradient(ellipse at 30% 25%, var(--marble-a) 0%, #efefee 45%, var(--marble-b) 100%);
  }
  .brand-mark { position: absolute; left: 72px; top: 118px; width: 236px; text-align: center; }
  .brand-name { font-family: "Cormorant Garamond", Georgia, serif; font-weight: 500; font-size: 64px; line-height: 1; color: var(--bronze); }
  .brand-place { font-family: "Montserrat", Arial, sans-serif; font-weight: 500; font-size: 8px; letter-spacing: 1.6px; color: var(--bronze); margin-top: 28px; padding-left: 80px; }

  .contact-block { position: absolute; left: 339px; top: 92px; }
  .person-name { font-family: "Playfair Display", Georgia, serif; font-weight: 600; font-size: 21px; letter-spacing: 0.5px; color: var(--bronze); line-height: 1.1; }
  .person-role { font-family: "Playfair Display", Georgia, serif; font-weight: 600; font-size: 15px; color: var(--muted); line-height: 1.1; }
  .address { font-size: 16px; line-height: 19px; margin-top: 9px; }
  .contact-list { list-style: none; margin-top: 8px; font-size: 16px; line-height: 19.5px; }
  .contact-list li { display: flex; align-items: center; gap: 7px; }
  .contact-list svg { width: 12px; height: 12px; fill: var(--bronze); flex: none; }

  /* Back */
  .card-back { left: 299px; top: 495px; background: var(--card-white); }
  .photo { position: absolute; }
  .photo-plants { left: 17px; top: 15px; width: 177px; height: 265px; background: linear-gradient(160deg, #f2f4f3 0%, #dfe3e0 55%, #c9d3c4 100%); }
  .photo-interior { left: 194px; top: 15px; width: 391px; height: 311px; background: linear-gradient(180deg, #eceae8 0%, #dedbd8 55%, #8d7d70 85%, #9a9a9a 100%); }
  .social-band { position: absolute; left: 17px; top: 280px; width: 177px; height: 46px; background: var(--bronze); color: #fff; display: flex; align-items: center; justify-content: space-between; padding: 0 10px; }
  .band-name { font-size: 22px; font-weight: 500; line-height: 1; }
  .social-list { list-style: none; font-size: 10px; line-height: 13px; font-weight: 600; display: flex; flex-direction: column; gap: 1px; }
  .social-list li { display: flex; align-items: center; gap: 4px; }
  .social-list li::before { content: ""; width: 6px; height: 6px; background: #fff; }
</style>
</head>
<body>
  <section class="card card-front" aria-label="Card front">
    <div class="marble-field" role="img" aria-label="White marble texture background"></div>
    <div class="brand-mark">
      <div class="brand-name">Lashvera</div>
      <div class="brand-place">ROSEWIND HILLS</div>
    </div>
    <div class="contact-block">
      <div class="person-name">MAREN HOLT</div>
      <div class="person-role">CEO/FOUNDER</div>
      <p class="address">4720 N.Alder Crest Ave<br>Rosewind Hills, CA 90315</p>
      <ul class="contact-list">
        <li><svg viewBox="0 0 12 12"><path d="M2.4 1 4.3 1 5 3.6 3.9 4.6a7 7 0 0 0 3.5 3.5L8.4 7l2.6.7v1.9c0 .6-.5 1.1-1.1 1.1A9 9 0 0 1 1.3 2.1C1.3 1.5 1.8 1 2.4 1Z"/></svg>310 555 0147</li>
        <li><svg viewBox="0 0 12 12"><path d="M1 2.5h10v7H1z"/><path d="M1 2.5 6 6.5l5-4" fill="none" stroke="#fff" stroke-width="0.9"/></svg>news@lashverastudio</li>
        <li><svg viewBox="0 0 12 12"><circle cx="6" cy="6" r="5.2"/><path d="M.8 6h10.4M6 .8c-2.4 2.8-2.4 7.6 0 10.4M6 .8c2.4 2.8 2.4 7.6 0 10.4" fill="none" stroke="#fff" stroke-width="0.8"/></svg>lashverastudio.example</li>
      </ul>
    </div>
  </section>

  <section class="card card-back" aria-label="Card back">
    <div class="photo photo-plants" role="img" aria-label="Photo of macrame plant hangers with green plants by a bright window"></div>
    <div class="photo photo-interior" role="img" aria-label="Photo of a bright white living room with fireplace, armchairs and wooden coffee table"></div>
    <div class="social-band">
      <span class="band-name">Lashvera</span>
      <ul class="social-list">
        <li>Circlebook</li>
        <li>Snapgrid</li>
      </ul>
    </div>
  </section>
</body>
</html>
```